Tidy paddock Services

After a high quality design website. we are a company that provides services to people that own land and need a hand getting on top of the delayed jobs.
would want a number of tab/ pages for the web page.
Home page / About us page / services page / Gallery page. / Contact us page
we offer a wide range of services .listed below

Stock Work (title)

Stock movement
Break feeding
Temporary staffing

Spraying (title)

Spraying weeds
Spraying gorse

Pastures (title)

Fertilizing
Topping

Building (title)

Habitable sheds
Farm sheds
Sheep yards
Cattle yards
Repair farm buildings
Decks
Retaining walls

Fencing (title)

Stock fencing
Post & rail
Stock yards repair
Electric fencing install & repairs

Water Management (title)

Water trough installation
Water scheme install
Water trough cleaning
Farm water maintenance
Water ponds
Ornamental ponds
Drainage

General (title)

Lawn mowing
Hedge trimming
Pruning trees
Metaling drive ways & races
Water blasting
Small digger work
Little tip truck cartage
Home kill management
Mulching gorse
Section clearing

```html
<!DOCTYPE html>
<html lang="en">
<head>
<meta charset="utf-8">
<title>Tidy paddock Services</title>
<link href="https://fonts.googleapis.com/css2?family=Poppins:wght@400;500;600;700&family=Roboto:wght@400;500&display=swap" rel="stylesheet">
<style>
:root{
  --green:#5e9b14;
  --green-dark:#4a7d0e;
  --ink:#222;
  --text:#333;
  --dark:#2a2a2a;
  --black:#000;
  --white:#fff;
  --grey:#e9e9e9;
}
*{box-sizing:border-box;margin:0;padding:0}
html,body{width:1200px;height:4320px;overflow:hidden}
body{position:relative;background:var(--white);font-family:"Roboto",Arial,sans-serif;color:var(--text)}
.abs{position:absolute}

/* header */
.site-header{position:absolute;left:0;top:0;width:1200px;height:94px;background:var(--white)}
.brand{position:absolute;display:flex;align-items:center;gap:8px;font-family:"Poppins",sans-serif;font-weight:600;color:var(--green)}
.brand-dot{width:14px;height:14px;border-radius:50%;background:var(--green)}
.site-header .brand{left:112px;top:30px;font-size:21px}
.main-nav{position:absolute;left:380px;top:34px;display:flex;gap:52px;font-size:15px}
.main-nav a{color:var(--ink);text-decoration:none}
.main-nav a.active{color:var(--green);font-weight:500;border-bottom:2px solid var(--green);padding-bottom:4px}
.btn{display:inline-block;background:var(--green);color:var(--white);font-family:"Poppins",sans-serif;font-weight:600;text-align:center;border-radius:24px;text-decoration:none}
.cta-start{position:absolute;left:906px;top:25px;width:109px;height:43px;line-height:43px;font-size:14px}
.header-social{position:absolute;left:1041px;top:39px;display:flex;gap:12px}
.header-social span{width:14px;height:14px;border-radius:50%;background:var(--green)}

/* hero */
.hero{position:absolute;left:0;top:94px;width:1200px;height:612px;overflow:hidden}
.hero-photo{position:absolute;inset:0;background:linear-gradient(180deg,#3f6b2c 0%,#5f8f3a 40%,#7eaf3b 75%,#8fbf34 100%)}
.hero-curve{position:absolute;left:0;top:0}
.hero-badge{position:absolute;left:160px;top:70px;width:440px;height:440px;border-radius:50%;background:rgba(80,150,20,.82);border:8px solid rgba(255,255,255,.85);text-align:center;color:var(--white);font-family:"Poppins",sans-serif}
.hero-badge .welcome{margin-top:122px;font-size:27px;font-weight:600}
.hero-badge h1{font-size:46px;line-height:56px;font-weight:700;margin-top:8px}
.hero-badge .learn{display:inline-block;margin-top:22px;border:2px solid var(--white);border-radius:24px;padding:10px 14px;font-size:13px;font-weight:600}
.hero-dots{position:absolute;left:571px;top:548px;display:flex;gap:8px}
.hero-dots span{width:13px;height:13px;border-radius:50%;background:var(--white)}
.hero-dots span.ring{background:transparent;border:2px solid var(--white)}

/* section heading */
.section-title{position:absolute;left:0;width:1200px;text-align:center;font-family:"Poppins",sans-serif;font-size:34px;font-weight:400;color:var(--ink);letter-spacing:.5px}
.section-title b{font-weight:700}
.title-bar{position:absolute;left:572px;width:56px;height:5px;background:var(--green)}

/* services */
.service-photo{position:absolute;width:505px;height:356px}
.service-card{position:absolute;width:494px;height:299px;background:var(--white);box-shadow:0 4px 24px rgba(0,0,0,.12);padding:38px 42px 20px}
.service-card--long{padding-top:20px}
.service-card h3{font-family:"Poppins",sans-serif;font-size:23px;line-height:34px;font-weight:500;color:var(--ink);margin-bottom:19px}
.service-card ul{list-style:none}
.service-card li{position:relative;padding-left:24px;font-size:15px;line-height:30px;color:var(--ink)}
.service-card li::before{content:"";position:absolute;left:0;top:8px;width:14px;height:14px;border-radius:50%;background:var(--green)}
.service-card li::after{content:"";position:absolute;left:4px;top:11px;width:5px;height:3px;border-left:2px solid var(--white);border-bottom:2px solid var(--white);transform:rotate(-45deg)}
.view-all{position:absolute;left:545px;top:2556px;width:110px;height:42px;line-height:42px;font-size:14px}

/* about */
.about{position:absolute;left:0;top:2685px;width:1200px;height:557px;background:var(--dark)}
.about-frame{position:absolute;left:115px;top:310px;width:229px;height:172px;border:2px solid #ddd;border-radius:10px}
.about-block{position:absolute;left:310px;top:73px;width:229px;height:165px;background:var(--green);border-radius:10px}
.about-photo{position:absolute;left:155px;top:100px;width:359px;height:340px;border-radius:12px;background:radial-gradient(circle at 55% 45%,#f2cf1a 0%,#d7a80c 45%,#4d5a2a 100%)}
.about h2{position:absolute;left:656px;top:92px;font-family:"Poppins",sans-serif;font-size:34px;font-weight:400;color:var(--white)}
.about h2 b{font-weight:700}
.about .bar{position:absolute;left:656px;top:143px;width:57px;height:5px;background:var(--green)}
.about p{position:absolute;left:656px;top:178px;width:434px;font-size:14.5px;line-height:25.7px;color:#e8e8e8}
.about .btn{position:absolute;left:656px;top:418px;width:110px;height:42px;line-height:42px;font-size:14px}

/* gallery */
.gallery-tile{position:absolute}

/* footer */
.site-footer{position:absolute;left:0;top:3890px;width:1200px;height:430px}
.site-footer .brand{left:0;width:1200px;justify-content:center;top:135px;font-size:30px;color:var(--white)}
.site-footer .brand-dot{background:var(--white);width:18px;height:18px}
.footer-nav{position:absolute;left:0;top:243px;width:1200px;text-align:center;font-size:15px;color:var(--white)}
.footer-nav a{color:var(--white);text-decoration:none}
.footer-nav .sep{margin:0 24px}
.footer-social{position:absolute;left:496px;top:300px;display:flex;gap:7px}
.footer-social span{width:36px;height:36px;border-radius:50%;border:2px solid var(--green)}
.copyright{position:absolute;left:0;top:370px;width:1200px;height:60px;background:var(--green);color:var(--white);font-size:15px;text-align:center;line-height:60px}
</style>
</head>
<body>

<header class="site-header">
  <div class="brand"><span class="brand-dot"></span>Tidy paddock Services</div>
  <nav class="main-nav">
    <a class="active" href="#">Home</a>
    <a href="#">About us</a>
    <a href="#">Services</a>
    <a href="#">Gallery</a>
    <a href="#">Contact us</a>
  </nav>
  <a class="btn cta-start" href="#">Get Started</a>
  <div class="header-social"><span></span><span></span></div>
</header>

<section class="hero">
  <div class="hero-photo" role="img" aria-label="Worker mowing a green lawn with a push mower beside garden shrubs"></div>
  <svg class="hero-curve" width="1200" height="612" viewBox="0 0 1200 612">
    <path d="M0 530 Q600 700 1200 530 L1200 612 L0 612 Z" fill="#fff"/>
    <path d="M0 530 Q600 700 1200 530 L1200 550 Q600 690 0 545 Z" fill="#5e9b14"/>
  </svg>
  <div class="hero-badge">
    <div class="welcome">WELCOME TO</div>
    <h1>TIDY PADDOCK<br>SERVICES</h1>
    <span class="learn">Learn More</span>
  </div>
  <div class="hero-dots"><span></span><span class="ring"></span><span></span></div>
</section>

<h2 class="section-title" style="top:780px"><b>OUR</b> SERVICES</h2>
<div class="title-bar" style="top:834px"></div>

<div class="service-photo" style="left:146px;top:890px;background:linear-gradient(135deg,#1f2a3a,#3a4f66 50%,#6c7a86)" role="img" aria-label="Man working at a computer with stock charts"></div>
<article class="service-card" style="left:560px;top:917px">
  <h3>Stock Work</h3>
  <ul><li>Stock movement</li><li>Break feeding</li><li>Temporary staffing</li></ul>
</article>

<div class="service-photo" style="left:549px;top:1303px;background:linear-gradient(135deg,#2f4a2a,#7fa66a 50%,#d8e4d4)" role="img" aria-label="Sprayer misting weeds in a garden"></div>
<article class="service-card" style="left:146px;top:1330px">
  <h3>Spraying</h3>
  <ul><li>Spraying weeds</li><li>Spraying gorse</li></ul>
</article>

<div class="service-photo" style="left:146px;top:1716px;background:linear-gradient(135deg,#6b4a2e,#9c8a52 50%,#a7b86a)" role="img" aria-label="Cattle grazing in a sunny pasture"></div>
<article class="service-card" style="left:560px;top:1743px">
  <h3>Pastures</h3>
  <ul><li>Fertilizing</li><li>Topping</li></ul>
</article>

<div class="service-photo" style="left:549px;top:2130px;background:linear-gradient(135deg,#6aa8e0,#3a6fb0 55%,#b98650)" role="img" aria-label="Modern building against a blue sky"></div>
<article class="service-card service-card--long" style="left:146px;top:2157px">
  <h3>Building</h3>
  <ul><li>Habitable sheds</li><li>Farm sheds</li><li>Sheep yards</li><li>Cattle yards</li><li>Repair farm buildings</li><li>Decks</li><li>Retaining walls</li></ul>
</article>

<a class="btn view-all" href="#">View All</a>

<section class="about">
  <div class="about-frame"></div>
  <div class="about-block"></div>
  <div class="about-photo" role="img" aria-label="Close up of yellow gorse flowers"></div>
  <h2><b>ABOUT</b> US</h2>
  <div class="bar"></div>
  <p>Lorem ipsum dolor sit amet, consectetur adipiscing elit, sed do eiusmod tempor incididunt ut labore et dolore magna aliqua. Ut enim ad minim veniam, quis nostrud exercitation ullamco laboris nisi ut aliquip ex ea commodo consequat. Duis aute irure dolor in reprehenderit in voluptate velit esse cillum dolore eu fugiat nulla pariatur. Excepteur sint occaecat cupidatat non proident, sunt in culpa qui officia deserunt mollit anim id est laborum.</p>
  <a class="btn" href="#">Learn More</a>
</section>

<h2 class="section-title" style="top:3318px"><b>OUR</b> GALLERY</h2>

<div class="gallery-tile" style="left:111px;top:3415px;width:451px;height:186px;background:linear-gradient(180deg,#c9d6d8,#8fa66a 45%,#4f7f2a)" role="img" aria-label="Tractor spraying a green crop field"></div>
<div class="gallery-tile" style="left:575px;top:3415px;width:324px;height:381px;background:linear-gradient(160deg,#5a5a40,#4f8a22 40%,#6fa82a)" role="img" aria-label="Hedge being trimmed with a hedge cutter"></div>
<div class="gallery-tile" style="left:913px;top:3415px;width:176px;height:179px;background:linear-gradient(160deg,#8fb050,#4a3a2a)" role="img" aria-label="Gloved hands planting a seedling in soil"></div>
<div class="gallery-tile" style="left:111px;top:3610px;width:177px;height:186px;background:linear-gradient(160deg,#e4ddd0,#9a8f80)" role="img" aria-label="Stacked bags of fertilizer on pallets"></div>
<div class="gallery-tile" style="left:303px;top:3610px;width:259px;height:186px;background:linear-gradient(160deg,#5c87b8,#c7883a 55%,#6a4a2a)" role="img" aria-label="Arborist pruning an autumn tree"></div>
<div class="gallery-tile" style="left:913px;top:3610px;width:176px;height:180px;background:linear-gradient(160deg,#e6d21a,#8a9a1a)" role="img" aria-label="Field of small yellow flowers"></div>

<footer class="site-footer">
  <svg class="abs" style="left:0;top:0" width="1200" height="370" viewBox="0 0 1200 370">
    <path d="M0 95 Q600 -40 1200 95 L1200 370 L0 370 Z" fill="#5e9b14"/>
    <path d="M0 100 Q600 -25 1200 100 L1200 370 L0 370 Z" fill="#000"/>
  </svg>
  <div class="brand"><span class="brand-dot"></span>Tidy paddock Services</div>
  <nav class="footer-nav">
    <a href="#">Home</a><span class="sep">|</span><a href="#">About us</a><span class="sep">|</span><a href="#">Services</a><span class="sep">|</span><a href="#">Gallery</a><span class="sep">|</span><a href="#">Contact us</a>
  </nav>
  <div class="footer-social"><span></span><span></span><span></span><span></span><span></span></div>
  <div class="copyright">©Copyrights 2024 Tidy paddock Services &nbsp; | &nbsp; All Rights Reserved</div>
</footer>

</body>
</html>
```